Flat Belly Design Graphics for Social

I want to create 9 social media graphics (new Instagram size 4:5 (1080 x 1350 pixels) focusing on our Flat Belly Graphics, using the pics attached. Use the attached pics, NO RANDOM STOCK PHOTOGRAPHY. For the color scheme of the graphics, the color palette is attached. YOU MUST POST ALL 9 GRAPHICS IN ONE ENTRY.
Using the 3 titles below, create one set of graphics. 1) with all text, then for the others, use the pictures as detailed below in IMPORTANT:
1. Ten-Week Bright Morning Reboot
2. The Quick Garden Kitchen Menu Guide
3. Studio Habits for Lasting Energy Past Midlife - Zero Gym Needed
IMPORTANT:
Only use RK Pic 1 and RK Pic 2 with the title, Ten-Week Bright Morning Reboot
Only use meal plan1 and meal plan2 pics with the title, Quick Garden Kitchen Menu Guide
Only use studio habits 1 and studio habits 2 pics with the title, Studio Habits for Lasting Energy Past Midlife - Zero Gym Needed
women over 40

```html
<!DOCTYPE html>
<html lang="en">
<head>
<meta charset="utf-8">
<title>Ten-Week Bright Morning Reboot – Social Set</title>
<link href="https://fonts.googleapis.com/css2?family=Plus+Jakarta+Sans:ital,wght@0,300;0,400;0,500;0,600;0,700;0,800;1,300;1,400;1,800&display=swap" rel="stylesheet">
<style>
  :root {
    --teal: #2e5955;
    --teal-deep: #24433f;
    --teal-slate: #34504c;
    --charcoal: #3a3c3d;
    --band: #394c4a;
    --pink: #e396ad;
    --pink-soft: #f3d5de;
    --cream: #fbf1f4;
    --white: #ffffff;
  }
  * { margin: 0; padding: 0; box-sizing: border-box; }
  html, body { width: 970px; height: 1200px; overflow: hidden; background: var(--white); }
  body { position: relative; font-family: "Plus Jakarta Sans", Arial, sans-serif; }

  .post {
    position: absolute; width: 427px; height: 531px; overflow: hidden;
    box-shadow: 0 10px 24px rgba(0,0,0,0.14);
  }
  .post--habits { left: 43px; top: 50px; background: radial-gradient(ellipse at 50% 40%, #2b5a55 0%, var(--teal-deep) 65%, #2d4a47 100%); }
  .post--reboot-title { left: 502px; top: 50px; background: radial-gradient(ellipse at 50% 45%, #2e625c 0%, var(--teal-slate) 80%); }
  .post--reboot-cover { left: 43px; top: 616px; background: linear-gradient(90deg, var(--charcoal) 0%, #353f3f 40%, var(--teal-slate) 100%); }
  .post--menu-guide { left: 502px; top: 616px; background: radial-gradient(ellipse at 50% 70%, #2d5a55 0%, var(--teal-slate) 90%); }

  .shape { position: absolute; inset: 0; width: 100%; height: 100%; }

  /* Studio habits post */
  .habits-title { position: absolute; top: 28px; left: 0; width: 100%; text-align: center; color: var(--pink); font-weight: 600; font-size: 41px; letter-spacing: -0.5px; text-shadow: 0 4px 14px rgba(0,0,0,0.35); }
  .habits-sub { position: absolute; top: 88px; left: 0; width: 100%; text-align: center; color: var(--cream); font-weight: 600; font-size: 17px; letter-spacing: -0.3px; text-shadow: 0 3px 10px rgba(0,0,0,0.35); }
  .habits-sub em { color: var(--pink); font-weight: 300; }
  .habits-tag { position: absolute; top: 127px; left: 0; width: 100%; text-align: center; color: var(--pink); font-weight: 600; font-size: 20px; }
  .habits-photo { position: absolute; left: 78px; top: 162px; width: 296px; height: 369px; border-radius: 120px 120px 0 0; background: linear-gradient(180deg, #4a3b36 0%, #c79a88 40%, #b28b87 60%, #4f6f92 100%); }

  /* Reboot title post */
  .title-band { position: absolute; left: 0; top: 204px; width: 100%; height: 123px; background: var(--band); }
  .title-week { position: absolute; top: 120px; left: 0; width: 100%; text-align: center; font-weight: 600; font-size: 74px; letter-spacing: -2px; text-shadow: 0 6px 16px rgba(0,0,0,0.3); }
  .title-week .accent { color: var(--pink); }
  .title-week .soft { color: var(--pink-soft); }
  .title-morning { position: absolute; top: 234px; left: 0; width: 100%; text-align: center; color: var(--pink); font-weight: 300; font-size: 42px; letter-spacing: -0.5px; }
  .title-reboot { position: absolute; top: 316px; left: 0; width: 100%; text-align: center; color: var(--pink-soft); font-weight: 700; font-size: 56px; letter-spacing: -1px; text-shadow: 0 6px 16px rgba(0,0,0,0.3); }

  /* Reboot cover post */
  .cover-spine { position: absolute; left: 385px; top: 0; width: 21px; height: 100%; background: var(--charcoal); }
  .cover-text { position: absolute; left: 38px; top: 172px; }
  .cover-week { color: var(--pink); font-weight: 600; font-size: 56px; letter-spacing: -1.5px; line-height: 1.1; }
  .cover-morning { color: var(--pink-soft); font-style: italic; font-weight: 300; font-size: 36px; letter-spacing: -0.5px; line-height: 1.3; margin-top: 4px; }
  .cover-reboot { color: var(--pink); font-weight: 600; font-size: 40px; letter-spacing: -1px; line-height: 1.3; margin-top: 6px; }

  /* Menu guide post */
  .menu-photo { position: absolute; left: 0; top: 0; width: 100%; height: 290px; background: linear-gradient(135deg, #d9b59f 0%, #6b3f2a 35%, #8a4a2f 55%, #c84a4a 75%, #4a2a1c 100%); clip-path: polygon(0 0, 100% 0, 100% 262px, 0 285px); }
  .menu-strip { position: absolute; left: -10px; top: 272px; width: 450px; height: 40px; background: var(--teal-slate); transform: rotate(-3deg); transform-origin: left top; display: flex; justify-content: space-around; align-items: center; color: var(--pink-soft); font-weight: 300; font-size: 17px; letter-spacing: -0.2px; }
  .menu-title { position: absolute; top: 345px; left: 0; width: 100%; text-align: center; }
  .menu-quick { color: var(--pink); font-style: italic; font-weight: 800; font-size: 38px; letter-spacing: -1px; line-height: 1.2; }
  .menu-garden { color: var(--pink); font-style: italic; font-weight: 300; font-size: 29px; line-height: 1.4; }
  .menu-guide { color: var(--cream); font-weight: 500; font-size: 32px; letter-spacing: -0.5px; line-height: 1.35; }
</style>
</head>
<body>

  <section class="post post--habits">
    <h2 class="habits-title">Studio Habits</h2>
    <p class="habits-sub">FOR <em>LASTING ENERGY</em> PAST MIDLIFE</p>
    <p class="habits-tag">Zero Gym Needed!</p>
    <div class="habits-photo" role="img" aria-label="Studio habits 1 photo: two women sharing a secret, one whispering and one smiling in surprise"></div>
  </section>

  <section class="post post--reboot-title">
    <svg class="shape" viewBox="0 0 427 531" preserveAspectRatio="none" aria-hidden="true">
      <path d="M0 0 H337 C210 22 60 45 0 89 Z" fill="var(--pink)"/>
      <path d="M427 461 C300 480 120 530 0 517 V531 H427 Z" fill="var(--pink)"/>
    </svg>
    <div class="title-band"></div>
    <h2 class="title-week"><span class="accent">Ten</span><span class="soft">-Week</span></h2>
    <p class="title-morning">Bright Morning</p>
    <p class="title-reboot">Reboot</p>
  </section>

  <section class="post post--reboot-cover">
    <svg class="shape" viewBox="0 0 427 531" preserveAspectRatio="none" aria-hidden="true">
      <defs>
        <linearGradient id="coverArc" x1="0" x2="1" y1="0" y2="0">
          <stop offset="0" stop-color="#3a3c3d" stop-opacity="0"/>
          <stop offset="0.35" stop-color="#5a5155"/>
          <stop offset="1" stop-color="#b9788c"/>
        </linearGradient>
        <clipPath id="coverClip"><rect x="0" y="0" width="362" height="531"/></clipPath>
      </defs>
      <circle cx="297" cy="330" r="206" fill="url(#coverArc)" clip-path="url(#coverClip)"/>
      <path d="M406 92 C418 100 424 108 427 112 V420 C420 428 413 434 406 438 Z" fill="#c98399"/>
    </svg>
    <div class="cover-spine"></div>
    <div class="cover-text">
      <h2 class="cover-week">Ten-Week</h2>
      <p class="cover-morning">BRIGHT MORNING</p>
      <p class="cover-reboot">Reboot</p>
    </div>
  </section>

  <section class="post post--menu-guide">
    <div class="menu-photo" role="img" aria-label="Meal plan 1 photo: fresh ingredients with a blank menu sheet on a wooden table"></div>
    <div class="menu-strip"><span>QUICK MENUS</span><span>GARDEN KITCHEN</span><span>QUICK MENUS</span></div>
    <div class="menu-title">
      <h2 class="menu-quick">The Quick</h2>
      <p class="menu-garden">Garden Kitchen</p>
      <p class="menu-guide">Menu Guide</p>
    </div>
  </section>

</body>
</html>
```